Social Media Templates for Fieldhouse Raffle Fund

We need a set of Square (1080 x 1080) social media posts.

My company works with sports clubs, helping them to raise money with a lottery.

I need a set of social media image that I can use to appeal to new Fieldhouse Raffle Fund to encourage them to start a lottery with us.

This landing page has worked very well for us https://fieldhouserafflefund.com/fieldhouse-raffle-fund/

THING THAT APPEAL TO CLUBS

No Setup Fees/Start for Free - (We don’t charge any registration fees, or setup fees so you can start raising money from the first draw.)

Start Straight Away - (A club can start raising money straight away.)

Sustainable Income - (The average player plays for 7 years)

Subscription Lottery - (once a player joins, they play until the choose to leave. A club doesn't have to sell tickets every draw to the same people)

All Administration Taken Care Of - (We do all the hard work, so they can focus on running their club.)

Unlimited Income - (There is no limit on the amount of money a club can raise: the more players, the more funds for the club.)

Fundraising reach - (Reach new fans)

50% of the sales is guaranteed profit

£25,000 jackpot - (a person could win £25,000 every week)

Price - (It costs just £1 per week to enter)

Help Your Club - (100% of the profit goes to the club who a player chooses to support)

You can see all the clubs we work with on www.fieldhouserafflefund.com

The images will also be used on Chatterwall. You can see some examples here https://www.chatterwall.com/FieldhouseRaffleFund/ (you may need a proxy to view this page as it is only viewable in the UK, so I have attached some screenshots)

You can find the Fieldhouse Raffle Fund Logo here https://www.logovault.com/winwellgroup/

Target Market(s)

People who are involved with amateur sports in United Kingdom

Industry/Entity Type

Gambling

Font styles to use
Sans Serif

Requirements
Must have
• My project must look great on social social media and encourage people to get in touch about starting a lottery with us.

Adobe Suite files must be provided

```html
<!DOCTYPE html>
<html lang="en">
<head>
<meta charset="utf-8">
<title>Fieldhouse Raffle Fund – Social Posts</title>
<link href="https://fonts.googleapis.com/css2?family=Oswald:wght@400;500;600;700&family=Montserrat:wght@400;800;900&family=Lilita+One&family=Roboto+Slab:wght@500;700&display=swap" rel="stylesheet">
<style>
  :root{
    --board:#2f2f31;
    --brand-blue:#2b7bbd;
    --sky:#8ecdf0;
    --navy:#0f2347;
    --orange:#f26a0c;
    --yellow:#ffe600;
    --red:#e8141c;
    --white:#ffffff;
    --ink:#222222;
    --grass-dark:#2f5e1c;
    --grass:#6aa531;
  }
  *{box-sizing:border-box;margin:0;padding:0}
  html,body{width:776px;height:1200px;overflow:hidden;background:var(--board)}
  .board{position:relative;width:776px;height:1200px;background:var(--board)}
  .post{position:absolute;width:321px;height:321px;overflow:hidden;box-shadow:0 3px 10px rgba(0,0,0,.35)}
  .col-a{left:43px}.col-b{left:400px}
  .row-1{top:63px}.row-2{top:440px}.row-3{top:808px}
  .abs{position:absolute}
  .photo{position:absolute}
  svg.layer{position:absolute;left:0;top:0}

  .brand{position:absolute;display:flex;align-items:center;gap:5px;font-family:"Oswald",sans-serif;font-weight:500;text-transform:uppercase;line-height:1.05}
  .brand .mark{flex:none;border-radius:2px}
  .brand--light{color:var(--white)}
  .brand--light .mark{background:var(--white)}
  .brand--blue{color:var(--brand-blue)}
  .brand--blue .mark{background:var(--brand-blue)}

  /* Post 1 */
  .p1 .photo{inset:0;background:linear-gradient(180deg,#10200c 0%,#27401c 28%,#6a8a7a 48%,#3f7fc0 60%,#5e9c30 78%,#4d8a26 100%)}
  .p1 .frame{left:8px;top:26px;width:305px;height:287px;border:2px solid var(--sky)}
  .p1 .tab{left:62px;top:13px;width:191px;height:27px;background:var(--sky);border-radius:14px;font-family:"Oswald",sans-serif;font-weight:600;font-size:22px;line-height:27px;text-align:center;color:var(--navy)}
  .p1 .jackpot{left:0;width:100%;top:42px;text-align:center;font-family:"Oswald",sans-serif;font-weight:700;font-size:36px;color:var(--white)}
  .p1 .price{left:0;width:100%;top:88px;text-align:center;font-family:"Oswald",sans-serif;font-weight:400;font-size:14px;color:var(--white);letter-spacing:.2px}
  .p1 .brand{left:140px;top:278px;width:80px;font-size:10px}
  .p1 .brand .mark{width:8px;height:8px}

  /* Post 2 */
  .p2 .photo.bg{inset:0;background:linear-gradient(160deg,#6fb8f2 0%,#8aa8f0 45%,#c08af0 100%)}
  .p2 .athlete{left:160px;top:28px;width:158px;height:275px;border-radius:70px 70px 40px 60px;background:linear-gradient(180deg,#3a2a22 0%,#1c2a2a 45%,#c08a5a 80%,#222 100%)}
  .p2 .banner{left:13px;top:48px;width:196px;height:27px;background:var(--yellow);transform:skewX(-8deg)}
  .p2 .banner span{display:block;transform:skewX(8deg);font-family:"Oswald",sans-serif;font-weight:700;font-style:italic;font-size:15px;line-height:27px;text-align:center;color:var(--red)}
  .p2 .subbanner{left:63px;top:74px;width:123px;height:14px;background:var(--red);transform:skewX(-8deg)}
  .p2 .subbanner span{display:block;transform:skewX(8deg);font-family:"Montserrat",sans-serif;font-weight:800;font-style:italic;font-size:10px;line-height:14px;text-align:center;color:var(--yellow)}
  .p2 .win{left:24px;top:94px;font-family:"Lilita One",sans-serif;font-size:27px;color:var(--yellow);-webkit-text-stroke:1px #3a2a00}
  .p2 .profit{left:26px;top:142px;font-family:"Roboto Slab",serif;font-weight:500;font-size:11px;color:var(--ink)}
  .p2 .rule{left:26px;top:158px;width:100px;height:1px;background:var(--ink)}
  .p2 .note{left:26px;top:162px;width:120px;font-family:"Roboto Slab",serif;font-weight:500;font-size:7.5px;line-height:10.5px;color:var(--ink)}
  .p2 .join{left:26px;top:193px;width:74px;height:17px;background:var(--yellow);border-radius:3px;font-family:"Roboto Slab",serif;font-weight:700;font-size:10.5px;line-height:17px;text-align:center;color:var(--ink)}
  .p2 .brand{left:27px;top:255px;width:70px;font-size:10px}
  .p2 .brand .mark{width:8px;height:8px}

  /* Post 3 */
  .p3{background:var(--navy)}
  .p3 .brand{left:22px;top:30px;width:80px;font-size:12px}
  .p3 .brand .mark{width:9px;height:9px}
  .p3 .dots{left:44px;top:90px;width:1px;height:110px;border-left:1px dotted rgba(255,255,255,.7);transform:rotate(12deg)}
  .p3 .kicker{left:26px;top:212px;font-family:"Oswald",sans-serif;font-weight:600;font-size:19px;color:var(--white)}
  .p3 .jackpot{left:26px;top:236px;font-family:"Oswald",sans-serif;font-weight:700;font-size:33px;color:var(--white)}
  .p3 .price{left:26px;top:274px;font-family:"Oswald",sans-serif;font-weight:700;font-size:22px;color:var(--yellow)}

  /* Post 4 */
  .p4{background:var(--white)}
  .p4 .brand{left:14px;top:20px;width:86px;font-size:13px}
  .p4 .brand .mark{width:10px;height:10px}
  .p4 .jackpot{left:109px;top:22px;font-family:"Montserrat",sans-serif;font-weight:900;font-size:20px;color:var(--orange)}
  .p4 .sub{left:109px;top:48px;font-family:"Montserrat",sans-serif;font-weight:400;font-size:9.5px;color:var(--ink)}
  .p4 .share{right:27px;top:104px;text-align:right;font-family:"Montserrat",sans-serif;color:var(--white);font-size:11.5px;line-height:13.5px}
  .p4 .share strong{font-weight:900;font-size:11px}

  /* Post 5 */
  .p5 .photo.grass{inset:0;background:linear-gradient(135deg,var(--grass-dark),var(--grass) 60%,var(--grass-dark))}
  .p5 .brand{left:24px;top:112px;width:100px;font-size:16px}
  .p5 .brand .mark{width:11px;height:11px}
  .p5 .headline{left:21px;top:208px;font-family:"Montserrat",sans-serif;font-weight:800;font-size:19px;line-height:25px;color:var(--brand-blue)}
  .p5 .body{left:21px;top:258px;width:190px;font-family:"Montserrat",sans-serif;font-weight:400;font-size:7.5px;line-height:10px;color:var(--ink)}

  /* Post 6 */
  .p6{background:var(--white)}
  .p6 .brand{left:24px;top:35px;width:88px;font-size:14px}
  .p6 .brand .mark{width:10px;height:10px}
  .p6 .headline{left:27px;top:178px;font-family:"Montserrat",sans-serif;font-weight:800;font-size:23px;line-height:31px;color:var(--white)}
  .p6 .body{left:27px;top:275px;width:170px;font-family:"Montserrat",sans-serif;font-weight:400;font-size:13.5px;line-height:17px;color:var(--white)}
</style>
</head>
<body>
<main class="board">

  <!-- Post 1: Start for free jackpot -->
  <section class="post p1 col-a row-1">
    <div class="photo" role="img" aria-label="Photo of children in blue and red kits playing football on a grass pitch"></div>
    <div class="abs frame"></div>
    <div class="abs tab">START FOR FREE</div>
    <div class="abs jackpot">£25,000 JACKPOT</div>
    <div class="abs price">£1 PER WEEK TO ENTER</div>
    <div class="brand brand--light"><span class="mark"></span><span>Fieldhouse Raffle Fund</span></div>
  </section>

  <!-- Post 2: Support a local sports club -->
  <section class="post p2 col-b row-1">
    <div class="photo bg" role="img" aria-label="Blue to purple background with faint sports doodles"></div>
    <svg class="layer" width="321" height="321" viewBox="0 0 321 321">
      <path d="M135 0 L321 0 L321 58 C290 40 270 20 230 16 C190 12 170 4 135 0 Z" fill="var(--yellow)"/>
      <path d="M135 0 C170 4 190 12 230 16 C270 20 290 40 321 58" fill="none" stroke="var(--red)" stroke-width="1.5"/>
      <path d="M130 321 C180 312 220 300 250 280 C280 258 300 235 321 225 L321 321 Z" fill="var(--yellow)"/>
      <path d="M130 321 C180 312 220 300 250 280 C280 258 300 235 321 225" fill="none" stroke="var(--red)" stroke-width="1.5"/>
    </svg>
    <div class="photo athlete" role="img" aria-label="Photo of a basketball player leaping with a ball"></div>
    <div class="abs banner"><span>Support a Local Sports Club</span></div>
    <div class="abs subbanner"><span>and You Could</span></div>
    <div class="abs win">Win £25,000</div>
    <div class="abs profit">100% of the profit</div>
    <div class="abs rule"></div>
    <div class="abs note">goes to the club who a player chooses to support</div>
    <div class="abs join">Join now ›</div>
    <div class="brand brand--light"><span class="mark"></span><span>Fieldhouse Raffle Fund</span></div>
  </section>

  <!-- Post 3: Team huddle jackpot -->
  <section class="post p3 col-a row-2">
    <svg class="layer" width="321" height="321" viewBox="0 0 321 321" role="img" aria-label="Photo of a coach with young players in blue kits celebrating together">
      <defs>
        <linearGradient id="huddle" x1="0" y1="0" x2="0" y2="1">
          <stop offset="0" stop-color="#d9dde0"/>
          <stop offset=".35" stop-color="#b08a6a"/>
          <stop offset=".6" stop-color="#1f3c82"/>
          <stop offset="1" stop-color="#0f2347"/>
        </linearGradient>
        <linearGradient id="fade" x1="0" y1="0" x2="0" y2="1">
          <stop offset="0" stop-color="#0f2347" stop-opacity="0"/>
          <stop offset="1" stop-color="#0f2347" stop-opacity=".85"/>
        </linearGradient>
      </defs>
      <polygon points="175,0 321,0 321,321 70,321 115,115" fill="url(#huddle)"/>
      <polygon points="110,0 175,0 115,115 90,80" fill="#13295a"/>
      <rect x="0" y="180" width="321" height="141" fill="url(#fade)"/>
      <polyline points="290,0 280,220 321,240" fill="none" stroke="#ffffff" stroke-width="1"/>
      <line x1="305" y1="200" x2="285" y2="321" stroke="#ffffff" stroke-width="1"/>
    </svg>
    <div class="brand brand--light"><span class="mark"></span><span>Fieldhouse Raffle Fund</span></div>
    <div class="abs dots"></div>
    <div class="abs kicker">START FOR FREE</div>
    <div class="abs jackpot">£25,000 JACKPOT</div>
    <div class="abs price">£1 PER WEEK TO ENTER</div>
  </section>

  <!-- Post 4: Jackpot with profit share -->
  <section class="post p4 col-b row-2">
    <svg class="layer" width="321" height="321" viewBox="0 0 321 321">
      <defs>
        <linearGradient id="pitch" x1="0" y1="0" x2="0" y2="1">
          <stop offset="0" stop-color="#e9ecef"/>
          <stop offset=".35" stop-color="#2a2d33"/>
          <stop offset=".55" stop-color="#8fb34a"/>
          <stop offset="1" stop-color="#6a9a2c"/>
        </linearGradient>
      </defs>
      <path d="M0 210 C60 110 190 75 321 75 L321 321 L0 321 Z" fill="var(--brand-blue)"/>
      <path d="M0 222 C70 160 170 140 230 155 C270 165 300 190 321 215 L321 321 L0 321 Z" fill="url(#pitch)" role="img" aria-label="Photo of a young boy in a blue kit kicking a football towards a goal"/>
    </svg>
    <div class="brand brand--blue"><span class="mark"></span><span>Fieldhouse Raffle Fund</span></div>
    <div class="abs jackpot">£25,000 JACKPOT</div>
    <div class="abs sub">A person could win £25,000 every week</div>
    <div class="abs share"><strong>100% OF THE PROFIT</strong><br>goes to the club who a player<br>chooses to support</div>
  </section>

  <!-- Post 5: No setup fees -->
  <section class="post p5 col-a row-3">
    <div class="photo grass" role="img" aria-label="Photo of artificial grass with a gold trophy in the corner"></div>
    <svg class="layer" width="321" height="321" viewBox="0 0 321 321">
      <defs>
        <linearGradient id="teamred" x1="0" y1="0" x2="0" y2="1">
          <stop offset="0" stop-color="#3e6a3a"/>
          <stop offset=".35" stop-color="#d8282e"/>
          <stop offset=".75" stop-color="#c41e24"/>
          <stop offset="1" stop-color="#5d8e3a"/>
        </linearGradient>
      </defs>
      <circle cx="28" cy="244" r="212" fill="none" stroke="var(--orange)" stroke-width="1.2"/>
      <circle cx="22" cy="248" r="206" fill="var(--white)"/>
      <circle cx="252" cy="100" r="112" fill="url(#teamred)" role="img" aria-label="Photo of a youth team in red kits in a huddle"/>
      <circle cx="252" cy="100" r="112" fill="none" stroke="#ffffff" stroke-opacity=".5" stroke-width="1"/>
    </svg>
    <div class="brand brand--blue"><span class="mark"></span><span>Fieldhouse Raffle Fund</span></div>
    <div class="abs headline">NO SETUP FEES/<br>START FOR FREE</div>
    <div class="abs body">We don't charge any registration fees, or setup fees so you can start raising money from the first draw.</div>
  </section>

  <!-- Post 6: Start straight away -->
  <section class="post p6 col-b row-3">
    <svg class="layer" width="321" height="321" viewBox="0 0 321 321">
      <defs>
        <linearGradient id="teamblue" x1="0" y1="0" x2="0" y2="1">
          <stop offset="0" stop-color="#a7b59a"/>
          <stop offset=".3" stop-color="#d9b08a"/>
          <stop offset=".55" stop-color="#2455b8"/>
          <stop offset="1" stop-color="#1a3d8a"/>
        </linearGradient>
      </defs>
      <polygon points="0,155 150,70 150,98 0,182" fill="var(--orange)"/>
      <polygon points="0,182 150,98 321,98 321,321 0,321" fill="var(--brand-blue)"/>
      <path d="M170 0 L321 0 L321 225 C300 215 270 218 250 228 C225 240 200 242 180 225 C150 200 140 150 142 100 C144 60 140 20 170 0 Z" fill="url(#teamblue)" role="img" aria-label="Photo of a youth team in blue kits huddled together"/>
    </svg>
    <div class="brand brand--blue"><span class="mark"></span><span>Fieldhouse Raffle Fund</span></div>
    <div class="abs headline">START<br>STRAIGHT<br>AWAY</div>
    <div class="abs body">A club can start raising money straight away.</div>
  </section>

</main>
</body>
</html>
```